Web Design for a Biotech Consulting Firm

We need a web site design for a new business based in Philadelphia called Verantel Dx. This is a consulting firm that will serve medical diagnostics industry, which is part of the life science/healthcare industry focusing on developing and marketing products that help in early detection, monitoring or management of diseases. Our consulting firm will help medical diagnostic companies to overcome key challenges in designing, evaluating and marketing new products.Our company name is Verantel Dx. Verantel is Latin word for "something" Dx represents diagnostics. The idea behind the name is that we help companies to transform the original, early product ideas ("nothing") into "something"; which is a product with full clinical utility that will help to improve health and well-being.The web site should use the visual feel of the logo (attached), be modern, simple and clean looking and represent creativity, innovation, scientific thinking and progress.
Updates

Wix Design is acceptable

Industry/Entity Type

Biotechnology

Coding

Coded - Design and coding required

Number of Pages Required

1 page

Font styles to use
Sans Serif

Requirements
Must have
• simple, clean look couple of pages
Should not have
• a lot of pages

```html
<!DOCTYPE html>
<html lang="en">
<head>
<meta charset="utf-8">
<title>Verantel Dx — Biotech Consulting Firm</title>
<link href="https://fonts.googleapis.com/css2?family=Montserrat:wght@400;500;600;700;800;900&display=swap" rel="stylesheet">
<style>
:root{
  --blue:#2270ee;
  --ink:#1c1c1c;
  --grey-text:#444;
  --soft:#f3f0f0;
  --tile:#dcdcdc;
  --tile-icon:#3a3a3a;
  --footer:#262626;
  --white:#fff;
}
*{box-sizing:border-box;margin:0;padding:0}
html,body{width:1200px;height:3766px;overflow:hidden}
body{font-family:'Montserrat',sans-serif;color:var(--ink);background:var(--white);position:relative}
.abs{position:absolute}
a{color:inherit;text-decoration:none}

/* header */
.site-header{position:absolute;left:0;top:0;width:1200px;height:122px;background:var(--white);z-index:3}
.brand-tab{position:absolute;left:123px;top:0;width:169px;height:200px;background:var(--white);z-index:4}
.brand-mark{position:absolute;left:12px;top:84px;width:12px;height:12px;background:var(--blue)}
.brand-name{position:absolute;left:32px;top:74px;font-size:24px;font-weight:600;color:var(--ink);white-space:nowrap}
.brand-tagline{position:absolute;left:12px;top:180px;font-size:9px;font-weight:700;color:var(--ink);letter-spacing:.3px}
.follow{position:absolute;left:723px;top:35px;font-size:10px;font-weight:700}
.social-dot{position:absolute;width:26px;height:26px;border-radius:50%}
.call-icon{position:absolute;left:891px;top:29px;width:28px;height:28px;border-radius:50%;background:#333}
.call-label{position:absolute;left:929px;top:24px;font-size:10px;font-weight:700}
.call-number{position:absolute;left:928px;top:36px;font-size:21px;font-weight:600;color:var(--blue)}
.main-nav a{position:absolute;top:81px;font-size:15px;font-weight:600}
.main-nav a.active{color:var(--blue);border-bottom:2px solid var(--blue);padding-bottom:2px}

/* hero */
.hero{position:absolute;left:0;top:122px;width:1200px;height:556px;background:linear-gradient(100deg,#41525f 0%,#6f8796 35%,#9bb3c4 60%,#c9d6de 85%,#e4e8ea 100%)}
.hero-title{position:absolute;left:131px;top:195px;font-size:54px;font-weight:900;line-height:56px;color:var(--white);letter-spacing:.5px}
.btn{display:block;position:absolute;background:var(--blue);color:var(--white);font-weight:700;text-align:center}
.hero-btn{left:134px;top:385px;width:156px;height:53px;line-height:49px;font-size:17px;border:2px solid var(--white)}
.dot{position:absolute;top:506px;width:10px;height:10px;border-radius:50%;background:var(--white)}
.dot.on{width:14px;height:14px;top:504px;background:transparent;border:3px solid var(--blue);box-shadow:0 0 0 2px var(--white) inset}

/* section titles */
.section-title{position:absolute;left:0;width:1200px;text-align:center;font-size:29px;font-weight:800;letter-spacing:-.3px}
.title-rule{position:absolute;left:578px;width:44px;height:3px;background:#999}

/* expertise */
.expertise{position:absolute;left:0;top:678px;width:1200px;height:630px;background:var(--soft)}
.tile{position:absolute;width:225px;height:190px;background:var(--tile);text-align:center}
.tile.active{background:var(--blue);color:var(--white)}
.tile svg{position:absolute;left:82px;top:30px}
.tile-label{position:absolute;left:0;top:118px;width:225px;font-size:15px;font-weight:600;line-height:21px}
.tag{position:absolute;width:87px;height:21px;line-height:21px;background:var(--blue);color:var(--white);font-size:10px;font-weight:700;text-align:center}

/* welcome */
.welcome-frame{position:absolute;left:133px;top:1362px;width:498px;height:497px;border:7px solid var(--blue)}
.frame-gap{position:absolute;left:622px;top:1517px;width:14px;height:186px;background:var(--white)}
.welcome-photo{position:absolute;left:159px;top:1390px;width:431px;height:441px;background:linear-gradient(135deg,#2d6f7a 0%,#6fb5a6 35%,#c9d98f 55%,#e79a8c 75%,#4b4f6d 100%)}
.welcome-kicker{position:absolute;left:675px;top:1397px;font-size:21px;font-weight:500}
.welcome-title{position:absolute;left:675px;top:1425px;font-size:41px;font-weight:800;letter-spacing:-.5px}
.welcome-rule{position:absolute;left:675px;top:1490px;width:46px;height:3px;background:#999}
.welcome-text{position:absolute;left:615px;top:1540px;width:445px;font-size:16px;line-height:23.3px;color:var(--grey-text)}
.welcome-btn{left:675px;top:1744px;width:143px;height:50px;line-height:50px;font-size:16px;font-weight:600}

/* stats */
.stats{position:absolute;left:0;top:1909px;width:1200px;height:361px;background:linear-gradient(90deg,#262626 0%,#333 50%,#2a2a2a 75%,#555 100%)}
.stat{position:absolute;top:76px;width:218px;height:222px;border:2px solid #d8d8d8;text-align:center;color:var(--white)}
.stat svg{position:absolute;left:82px;top:34px}
.stat-num{position:absolute;left:0;top:100px;width:214px;font-size:29px;font-weight:800;color:var(--blue)}
.stat-label{position:absolute;left:0;top:149px;width:214px;font-size:15px;font-weight:500;line-height:21px}

/* news */
.news{position:absolute;left:0;top:2270px;width:1200px;height:602px;background:#ececec}
.news-photo{position:absolute;top:164px;width:271px;height:226px}
.news-card{position:absolute;top:357px;width:247px;height:176px;background:var(--white);box-shadow:0 2px 4px rgba(0,0,0,.18)}
.news-card h3{position:absolute;left:29px;top:22px;font-size:15px;font-weight:700}
.news-card p{position:absolute;left:29px;top:48px;width:200px;font-size:11.5px;line-height:17px;color:var(--grey-text)}
.news-btn{left:29px;top:119px;width:101px;height:32px;line-height:32px;font-size:11px}

/* testimonials */
.quote-card{position:absolute;top:3037px;width:453px;height:298px;background:var(--soft)}
.quote-mark{position:absolute;left:33px;top:28px;font-size:60px;font-weight:900;color:var(--blue);line-height:60px}
.quote-text{position:absolute;left:76px;top:60px;width:320px;font-size:17px;line-height:24px;color:#222}
.avatar{position:absolute;left:72px;top:218px;width:46px;height:46px;border-radius:50%;background:#c9b8a8}
.quote-name{position:absolute;left:134px;top:228px;font-size:14px;font-weight:700;color:var(--blue)}
.quote-city{position:absolute;left:134px;top:249px;font-size:12px}
.slider-arrow{position:absolute;top:3176px}

/* footer */
.site-footer{position:absolute;left:0;top:3398px;width:1200px;height:368px;background:var(--footer);color:var(--white)}
.foot-mark{position:absolute;left:175px;top:160px;width:18px;height:18px;background:var(--blue)}
.foot-brand{position:absolute;left:205px;top:141px;font-size:44px;font-weight:600;white-space:nowrap}
.foot-tagline{position:absolute;left:175px;top:298px;font-size:13px;font-weight:700;letter-spacing:.3px}
.foot-head{position:absolute;top:58px;font-size:11px;font-weight:700}
.foot-line{position:absolute;font-size:10.5px;line-height:17px}
.foot-social{position:absolute;left:950px;width:26px;height:26px;border-radius:50%;background:var(--blue)}
.copyright{position:absolute;left:854px;top:306px;font-size:10px}
</style>
</head>
<body>

<header class="site-header">
  <div class="follow">FOLLOW US</div>
  <span class="social-dot" style="left:801px;top:28px;background:#3b5aa0"></span>
  <span class="social-dot" style="left:836px;top:28px;background:#1e9be0"></span>
  <span class="call-icon">
    <svg width="28" height="28" viewBox="0 0 28 28"><path d="M10 8c1 0 2 2 2 3s-1 1-1 2c1 2 2 3 4 4 1 0 1-1 2-1s3 1 3 2c0 2-2 3-3 3-5 0-10-5-10-10 0-1 1-3 3-3z" fill="#fff"/></svg>
  </span>
  <div class="call-label">CALL US</div>
  <div class="call-number">555.014.2290</div>
  <nav class="main-nav">
    <a class="active" style="left:584px">Home</a>
    <a style="left:661px">About Us</a>
    <a style="left:764px">Services</a>
    <a style="left:868px">Resources</a>
    <a style="left:982px">Contact Us</a>
  </nav>
</header>

<div class="brand-tab">
  <span class="brand-mark"></span>
  <div class="brand-name">Verantel Dx</div>
  <div class="brand-tagline">DIAGNOSTICS CONSULTING</div>
</div>

<section class="hero">
  <div class="abs" role="img" aria-label="Scientist in blue gloves holding a petri dish in a laboratory" style="inset:0"></div>
  <h1 class="hero-title">BIOTECH<br>CONSULTING<br>FIRM</h1>
  <a class="btn hero-btn">READ MORE</a>
  <span class="dot" style="left:548px"></span>
  <span class="dot" style="left:572px"></span>
  <span class="dot on" style="left:593px"></span>
  <span class="dot" style="left:619px"></span>
  <span class="dot" style="left:643px"></span>
</section>

<section class="expertise">
  <h2 class="section-title" style="top:40px">OUR EXPERTISE</h2>
  <div class="title-rule" style="top:88px"></div>

  <div class="tile" style="left:130px;top:130px">
    <svg width="60" height="60" viewBox="0 0 60 60"><path d="M12 4h26l10 10v42H12z" fill="var(--tile-icon)"/><path d="M18 22h18M18 30h14M18 38h12M18 46h16" stroke="#dcdcdc" stroke-width="3"/><circle cx="42" cy="40" r="8" fill="#dcdcdc" stroke="var(--tile-icon)" stroke-width="3"/></svg>
    <div class="tile-label">Pharmaceutical<br>Reports</div>
  </div>
  <div class="tag" style="left:268px;top:320px">READ MORE</div>

  <div class="tile" style="left:368px;top:130px">
    <svg width="64" height="60" viewBox="0 0 64 60"><path d="M12 30c-6-2-6-12 2-14 0-8 10-10 14-6 4-5 14-4 16 2 8 0 12 8 8 14 4 6-2 14-10 12-4 6-14 4-16-2-6 2-14-2-14-6z" fill="none" stroke="var(--tile-icon)" stroke-width="4"/><circle cx="24" cy="26" r="3" fill="var(--tile-icon)"/><circle cx="38" cy="22" r="3" fill="var(--tile-icon)"/><circle cx="34" cy="36" r="3" fill="var(--tile-icon)"/><path d="M30 44v12" stroke="var(--tile-icon)" stroke-width="4"/></svg>
    <div class="tile-label">Competitive<br>Intelligence</div>
  </div>
  <div class="tag" style="left:506px;top:320px">READ MORE</div>

  <div class="tile active" style="left:604px;top:130px">
    <svg width="60" height="60" viewBox="0 0 60 60"><rect x="4" y="4" width="52" height="36" fill="none" stroke="#fff" stroke-width="3"/><rect x="4" y="4" width="52" height="6" fill="#fff"/><path d="M36 34v-8M42 34v-12M48 34v-16" stroke="#fff" stroke-width="3"/><circle cx="20" cy="24" r="7" fill="none" stroke="#fff" stroke-width="3"/><path d="M30 40v4M30 44l-10 12M30 44l10 12" stroke="#fff" stroke-width="3"/></svg>
    <div class="tile-label">Corporate<br>Strategy</div>
  </div>
  <div class="tag" style="left:742px;top:320px">READ MORE</div>

  <div class="tile" style="left:840px;top:130px">
    <svg width="60" height="60" viewBox="0 0 60 60"><path d="M30 12a14 14 0 0 0-8 25v7h16v-7a14 14 0 0 0-8-25z" fill="var(--tile-icon)"/><rect x="24" y="47" width="12" height="6" fill="var(--tile-icon)"/><path d="M30 2v6M10 10l4 4M50 10l-4 4M4 28h6M50 28h6" stroke="var(--tile-icon)" stroke-width="3"/></svg>
    <div class="tile-label">Intelligence</div>
  </div>
  <div class="tag" style="left:978px;top:320px">READ MORE</div>

  <div class="tile" style="left:130px;top:363px">
    <svg width="60" height="60" viewBox="0 0 60 60"><g stroke="var(--tile-icon)" stroke-width="4"><path d="M30 30L12 12M30 30L48 12M30 30L12 48M30 30L48 48M30 30L8 30"/></g><circle cx="30" cy="30" r="8" fill="var(--tile-icon)"/><circle cx="12" cy="12" r="6" fill="var(--tile-icon)"/><circle cx="48" cy="12" r="6" fill="var(--tile-icon)"/><circle cx="12" cy="48" r="6" fill="var(--tile-icon)"/><circle cx="48" cy="48" r="6" fill="var(--tile-icon)"/></svg>
    <div class="tile-label">Sciences /<br>Technology</div>
  </div>
  <div class="tag" style="left:268px;top:553px">READ MORE</div>

  <div class="tile" style="left:368px;top:363px">
    <svg width="60" height="60" viewBox="0 0 60 60"><path d="M14 4h32v52H14z" fill="none" stroke="var(--tile-icon)" stroke-width="3"/><path d="M20 14h20M20 20h20M20 26h14" stroke="var(--tile-icon)" stroke-width="3"/><circle cx="24" cy="42" r="7" fill="none" stroke="var(--tile-icon)" stroke-width="3"/><path d="M34 44h8" stroke="var(--tile-icon)" stroke-width="3"/></svg>
    <div class="tile-label">Legal &amp;<br>Intellectual property</div>
  </div>
  <div class="tag" style="left:506px;top:553px">READ MORE</div>

  <div class="tile" style="left:604px;top:363px">
    <svg width="60" height="60" viewBox="0 0 60 60"><rect x="24" y="2" width="12" height="12" fill="var(--tile-icon)"/><rect x="24" y="24" width="12" height="12" fill="var(--tile-icon)"/><rect x="4" y="44" width="12" height="12" fill="var(--tile-icon)"/><rect x="24" y="44" width="12" height="12" fill="var(--tile-icon)"/><rect x="44" y="44" width="12" height="12" fill="var(--tile-icon)"/><path d="M30 14v10M30 36v8M10 44v-4h40v4" fill="none" stroke="var(--tile-icon)" stroke-width="3"/></svg>
    <div class="tile-label">Private &amp; public<br>organisations</div>
  </div>
  <div class="tag" style="left:742px;top:553px">READ MORE</div>

  <div class="tile" style="left:840px;top:363px">
    <svg width="70" height="60" viewBox="0 0 70 60"><path d="M6 56V36h8v20M20 56V26h8v30M34 56V32h8v24M48 56V18h8v38" fill="var(--tile-icon)"/><path d="M4 34l16-18 14 12 22-22" fill="none" stroke="var(--tile-icon)" stroke-width="4"/><path d="M52 2h10v10" fill="none" stroke="var(--tile-icon)" stroke-width="4"/></svg>
    <div class="tile-label">R&amp;D Analytics</div>
  </div>
  <div class="tag" style="left:978px;top:553px">READ MORE</div>
</section>

<section class="welcome">
  <div class="welcome-frame"></div>
  <div class="frame-gap"></div>
  <div class="welcome-photo" role="img" aria-label="Laboratory glassware with glowing molecular diagram overlay"></div>
  <div class="welcome-kicker">WELCOME TO</div>
  <h2 class="welcome-title">VERANTEL DX</h2>
  <div class="welcome-rule"></div>
  <p class="welcome-text">Lorem ipsum dolor sit amet, consectetur adipiscing elit, sed do eiusmod tempor incididunt ut labore et dolore magna aliqua. Ut enim ad minim veniam, quis nostrud exercitation ullamco laboris nisi ut aliquip ex ea commodo consequat. Duis aute irure dolor in reprehenderit in voluptate velit esse cillum dolore eu fugiatA</p>
  <a class="btn welcome-btn">READ MORE</a>
</section>

<section class="stats">
  <div class="abs" role="img" aria-label="Dimmed laboratory background photo" style="inset:0"></div>
  <div class="stat" style="left:130px">
    <svg width="52" height="52" viewBox="0 0 52 52"><rect x="4" y="4" width="44" height="32" rx="3" fill="none" stroke="#fff" stroke-width="3"/><circle cx="26" cy="20" r="8" fill="none" stroke="#fff" stroke-width="3"/><path d="M10 12h6M10 18h6M36 12h6M36 18h6M26 36v8M16 48h20" stroke="#fff" stroke-width="3"/></svg>
    <div class="stat-num">2541</div>
    <div class="stat-label">Pharma Reports</div>
  </div>
  <div class="stat" style="left:373px">
    <svg width="60" height="52" viewBox="0 0 60 52"><circle cx="22" cy="14" r="10" fill="#fff"/><circle cx="40" cy="16" r="9" fill="#fff"/><path d="M2 48c0-14 8-20 20-20s20 6 20 20z" fill="#fff"/><path d="M44 48c0-10-2-14-6-18 14 0 20 6 20 18z" fill="#fff"/></svg>
    <div class="stat-num">415</div>
    <div class="stat-label">Clients</div>
  </div>
  <div class="stat" style="left:614px">
    <svg width="52" height="52" viewBox="0 0 52 52"><circle cx="26" cy="26" r="24" fill="#fff"/><path d="M14 12c6 2 10 6 8 12-4 2-8 0-10 6-4-4-6-12 2-18zM32 30c6 0 8 4 6 10-4 4-8 2-8-2 0-4-2-6 2-8z" fill="#2c2c2c"/></svg>
    <div class="stat-num">415</div>
    <div class="stat-label">Major Pharma<br>Markets Coverage</div>
  </div>
  <div class="stat" style="left:854px">
    <svg width="56" height="52" viewBox="0 0 56 52"><path d="M20 10V4h16v6" fill="none" stroke="#fff" stroke-width="4"/><rect x="2" y="10" width="52" height="38" rx="4" fill="#fff"/><rect x="23" y="24" width="10" height="8" fill="#2c2c2c"/><path d="M2 26h52" stroke="#2c2c2c" stroke-width="2"/></svg>
    <div class="stat-num">15+</div>
    <div class="stat-label">Years Experience</div>
  </div>
</section>

<section class="news">
  <h2 class="section-title" style="top:66px">LATEST NEWS</h2>
  <div class="title-rule" style="top:110px"></div>

  <div class="news-photo" role="img" aria-label="Gloved hands adjusting a laboratory microscope" style="left:156px;background:linear-gradient(135deg,#dfe7f2,#7a95bd 55%,#f2f2f2)"></div>
  <article class="news-card" style="left:170px">
    <h3>Lorem Ipsum is simply</h3>
    <p>Sed ut perspiciatis unde omnis iste natus error sit voluptatem accusantium doloremque.</p>
    <a class="btn news-btn">READ MORE</a>
  </article>

  <div class="news-photo" role="img" aria-label="Consultant presenting in a bright office" style="left:468px;background:linear-gradient(180deg,#e9ecef,#b7c0c8 50%,#5d6670)"></div>
  <article class="news-card" style="left:481px">
    <h3>Lorem Ipsum is simply</h3>
    <p>Sed ut perspiciatis unde omnis iste natus error sit voluptatem accusantium doloremque.</p>
    <a class="btn news-btn">READ MORE</a>
  </article>

  <div class="news-photo" role="img" aria-label="Gloved hand writing with a pen on a lab report" style="left:782px;background:linear-gradient(135deg,#4c5560,#9aa7b6 50%,#7fa4d8)"></div>
  <article class="news-card" style="left:795px">
    <h3>Lorem Ipsum is simply</h3>
    <p>Sed ut perspiciatis unde omnis iste natus error sit voluptatem accusantium doloremque.</p>
    <a class="btn news-btn">READ MORE</a>
  </article>
</section>

<section class="testimonials">
  <h2 class="section-title" style="top:2930px">WHAT OUR CLIENTS SAY</h2>
  <div class="title-rule" style="top:2986px"></div>

  <svg class="slider-arrow" style="left:88px" width="16" height="24" viewBox="0 0 16 24"><path d="M13 2L3 12l10 10" fill="none" stroke="#888" stroke-width="2"/></svg>
  <svg class="slider-arrow" style="left:1098px" width="16" height="24" viewBox="0 0 16 24"><path d="M3 2l10 10-10 10" fill="none" stroke="#888" stroke-width="2"/></svg>

  <blockquote class="quote-card" style="left:132px">
    <div class="quote-mark">“</div>
    <p class="quote-text">Sed ut perspiciatis unde omnis iste n atus error sit voluptatem accusantium doloremque laudantium, totam rem aperiam, eaque ipsa quae ab illo inventore veritatis et quasi</p>
    <span class="avatar" role="img" aria-label="Client portrait"></span>
    <div class="quote-name">MARCUS</div>
    <div class="quote-city">Los Angels</div>
  </blockquote>

  <blockquote class="quote-card" style="left:615px">
    <div class="quote-mark">“</div>
    <p class="quote-text">Sed ut perspiciatis unde omnis iste n atus error sit voluptatem accusantium doloremque laudantium, totam rem aperiam, eaque ipsa quae ab illo inventore veritatis et quasi</p>
    <span class="avatar" role="img" aria-label="Client portrait"></span>
    <div class="quote-name">MARCUS</div>
    <div class="quote-city">Los Angels</div>
  </blockquote>
</section>

<footer class="site-footer">
  <span class="foot-mark"></span>
  <div class="foot-brand">Verantel Dx</div>
  <div class="foot-tagline">DIAGNOSTICS CONSULTING</div>

  <div class="foot-head" style="left:528px">CONTACT US</div>
  <svg class="abs" style="left:526px;top:92px" width="10" height="12" viewBox="0 0 10 12"><path d="M5 0a4 4 0 0 1 4 4c0 3-4 8-4 8S1 7 1 4a4 4 0 0 1 4-4z" fill="#fff"/><circle cx="5" cy="4" r="1.5" fill="#262626"/></svg>
  <div class="foot-line" style="left:548px;top:89px">2210 Harlow Street<br>Philadelphia, PA 19103</div>
  <svg class="abs" style="left:526px;top:143px" width="11" height="11" viewBox="0 0 28 28"><path d="M8 2c2 0 4 5 4 6s-2 2-2 3c2 3 4 5 7 7 1 0 2-2 3-2s6 2 6 4c0 3-3 6-6 6C10 26 2 18 2 8c0-3 3-6 6-6z" fill="#fff"/></svg>
  <div class="foot-line" style="left:548px;top:140px">555.014.2290</div>
  <svg class="abs" style="left:526px;top:180px" width="12" height="9" viewBox="0 0 12 9"><rect width="12" height="9" fill="#fff"/><path d="M0 0l6 5 6-5" fill="none" stroke="#262626"/></svg>
  <div class="foot-line" style="left:550px;top:176px">info@verantelDx.com</div>

  <div class="foot-head" style="left:763px">MENU</div>
  <div class="foot-line" style="left:763px;top:89px">HOME<br>ABOUT US<br>SERVICES<br>RESOURCES<br>CONTACT US</div>

  <div class="foot-head" style="left:950px">CONNECT WITH US</div>
  <span class="foot-social" style="top:94px"></span>
  <div class="foot-line" style="left:990px;top:99px">Community</div>
  <span class="foot-social" style="top:134px"></span>
  <div class="foot-line" style="left:990px;top:139px">News Feed</div>
  <span class="foot-social" style="top:173px"></span>
  <div class="foot-line" style="left:990px;top:178px">Careers</div>

  <div class="copyright">Copyrights @ 2019 All Rights Reserved</div>
</footer>

</body>
</html>
```